Brightarc Orthodontics appointment card design

I need appointment cards/ business cards made. Front will be Logo, name, title, email, phone number and location (5263 Walnut Hollow Pkwy, Ste 412, Concord, NC 28027) . the back should have an appointment card (name, time, date) and also 3 addresses listed with a check box so we can check to which location they are going.
Dale Fenwick Orthodontics
- 6735 Orchard Street, Ste 514, Harrisburg, NC 28075
- 3647 Ridgeway Drive NE, Ste 810, Concord, NC 28025
- 2917 Thornbury Corporate Drive, Ste 605, Charlotte, NC 28277
Business card can be horizontal or vertical in Design.
I need to be able to edit it to update and add new employees

Requirements
Must have
• Front:
• - Logo
• - Name & Title (able to be edited)
• - phone (704-555-0186) & Email (need to be able to edit)
• - Address: 5263 Walnut Hollow Pkwy, Ste 412
• Concord, NC 28027
• Back:
• Appointment Card design:
• - Name, time, Date
• - 3 locations w/ a check box so the patient knows where to go:
• Dale Fenwick Orthodontics
• - 6735 Orchard Street, Ste 514, Harrisburg, NC 28075
• - 3647 Ridgeway Drive NE, Ste 810, Concord, NC 28025
• - 2917 Thornbury Corporate Drive, Ste 605, Charlotte, NC 28277

```html
<!DOCTYPE html>
<html lang="en">
<head>
<meta charset="utf-8">
<title>Brightarc Orthodontics – Business &amp; Appointment Card</title>
<link href="https://fonts.googleapis.com/css2?family=Lato:wght@400;700;900&family=Oswald:wght@600&display=swap" rel="stylesheet">
<style>
  :root {
    --backdrop: #2a2b2d;
    --card-light: #c8c8c8;
    --card-dark: #1c1c1e;
    --brand-blue: #1f78c8;
    --ink: #1a1a1a;
    --ink-soft: #2b2b2b;
    --paper: #ffffff;
    --rule-blue: #2e5fb0;
  }
  * { box-sizing: border-box; margin: 0; padding: 0; }
  html, body { width: 1200px; height: 1200px; overflow: hidden; }
  body {
    background: var(--backdrop);
    font-family: "Lato", sans-serif;
    display: flex;
    flex-direction: column;
    align-items: center;
    justify-content: center;
    gap: 60px;
  }
  .card {
    position: relative;
    width: 860px;
    height: 491px;
    border-radius: 4px;
    overflow: hidden;
  }

  /* ---------- Front ---------- */
  .card--front { background: var(--card-light); color: var(--ink); }
  .brand {
    position: absolute;
    display: flex;
    align-items: center;
    gap: 14px;
    color: var(--brand-blue);
    font-weight: 900;
    line-height: 1.02;
  }
  .brand__dot {
    width: 22px; height: 22px;
    border-radius: 50%;
    background: var(--brand-blue);
    flex: none;
  }
  .card--front .brand { left: 70px; top: 196px; font-size: 44px; }
  .divider {
    position: absolute;
    left: 430px; top: 150px;
    width: 2px; height: 190px;
    background: var(--brand-blue);
  }
  .contact {
    position: absolute;
    left: 462px; top: 150px;
    font-size: 17px;
    line-height: 1.32;
  }
  .contact__name {
    font-family: "Oswald", sans-serif;
    font-weight: 600;
    font-size: 30px;
    line-height: 1.1;
    text-transform: uppercase;
    color: var(--ink);
  }
  .contact__title { color: var(--brand-blue); font-size: 18px; margin-bottom: 6px; }
  .contact__row { display: flex; align-items: center; gap: 8px; }
  .contact__row svg { width: 14px; height: 14px; flex: none; }

  /* ---------- Back ---------- */
  .card--back { background: var(--card-dark); color: var(--paper); }
  .card--back .brand { left: 60px; top: 54px; font-size: 40px; }
  .appointment {
    position: absolute;
    left: 60px; top: 178px;
    width: 740px; height: 118px;
    background: var(--paper);
    border-radius: 14px;
    color: var(--ink);
    padding: 20px 28px;
    display: flex;
    flex-direction: column;
    justify-content: space-between;
    font-weight: 900;
    font-size: 21px;
  }
  .appointment__row { display: flex; align-items: flex-end; gap: 10px; }
  .appointment__line { flex: 1; border-bottom: 1.5px solid var(--rule-blue); height: 20px; }
  .appointment__suffix { font-weight: 400; font-size: 19px; }
  .locations {
    position: absolute;
    left: 60px; top: 318px;
    list-style: none;
    font-size: 20px;
    line-height: 1.5;
  }
  .locations__heading { font-weight: 900; font-size: 21px; margin-left: 34px; }
  .locations__item { display: flex; align-items: center; gap: 14px; }
  .checkbox {
    width: 20px; height: 20px;
    background: var(--paper);
    border: 2px solid var(--paper);
    flex: none;
  }
  .checkbox--active { background: var(--brand-blue); border-color: var(--brand-blue); }
</style>
</head>
<body>

  <section class="card card--front" aria-label="Business card front">
    <div class="brand"><span class="brand__dot"></span><span>Brightarc<br>Orthodontics</span></div>
    <div class="divider"></div>
    <div class="contact">
      <div class="contact__name">Nolan Price</div>
      <div class="contact__title">CEO / Manager</div>
      <div>5263 Walnut Hollow Pkwy</div>
      <div>Ste 412 - Concord, NC 28027</div>
      <div class="contact__row">
        <svg viewBox="0 0 24 24" fill="#1f78c8"><path d="M6.6 10.8a15.1 15.1 0 0 0 6.6 6.6l2.2-2.2a1 1 0 0 1 1-.25 11.4 11.4 0 0 0 3.6.57 1 1 0 0 1 1 1V20a1 1 0 0 1-1 1A17 17 0 0 1 3 4a1 1 0 0 1 1-1h3.5a1 1 0 0 1 1 1c0 1.25.2 2.45.57 3.57a1 1 0 0 1-.25 1z"/></svg>
        <span>+704-555-0186</span>
      </div>
      <div class="contact__row">
        <svg viewBox="0 0 24 24" fill="none" stroke="#1f78c8" stroke-width="2"><circle cx="12" cy="12" r="9"/><path d="M3 12h18M12 3c3 3.5 3 14.5 0 18M12 3c-3 3.5-3 14.5 0 18"/></svg>
        <span>www.brightarcortho.com</span>
      </div>
      <div class="contact__row">
        <svg viewBox="0 0 24 24" fill="#1f78c8"><path d="M2 5h20v14H2z"/><path d="M2 5l10 8 10-8" fill="none" stroke="#c8c8c8" stroke-width="1.6"/></svg>
        <span>hello@brightarcortho.com</span>
      </div>
    </div>
  </section>

  <section class="card card--back" aria-label="Appointment card back">
    <div class="brand"><span class="brand__dot"></span><span>Brightarc<br>Orthodontics</span></div>
    <div class="appointment">
      <div class="appointment__row">
        <span>Name :</span><span class="appointment__line"></span>
        <span>Date :</span><span class="appointment__line" style="flex:0 0 200px"></span>
      </div>
      <div class="appointment__row">
        <span>Time :</span><span class="appointment__line"></span>
        <span class="appointment__suffix">AM/PM</span>
      </div>
    </div>
    <ul class="locations">
      <li class="locations__heading">Dale Fenwick Orthodontics :</li>
      <li class="locations__item"><span class="checkbox checkbox--active"></span>6735 Orchard Street, Ste 514, Harrisburg, NC 28075</li>
      <li class="locations__item"><span class="checkbox"></span>3647 Ridgeway Drive NE, Ste 810, Concord, NC 28025</li>
      <li class="locations__item"><span class="checkbox"></span>2917 Thornbury Corporate Drive, Ste 605, Charlotte, NC 28277</li>
    </ul>
  </section>

</body>
</html>
```